Redesign a Start-Up Dating Website

Website: https://morvelique.com.
Make sure the design has an island style theme.
I would like the 7 pages of my website to have a new and professional look. I want the same colors to remain, but I want a creative look for all the pages. This is a dating website that is in the startup stage. So, I want to give my entire website a custom makeover. I want something that will stand out from the other dating sites. Something that will attract more people to want to use my services, and hopefully get new members.
Target Market(s)
Dating
Industry/Entity Type
Dating
Coding
Coded - Design and coding required
Number of Pages Required
5+ page
Font styles to use
Other font styles liked:
- Decorative, San Serif
Requirements
Must have
- The design must have the original colors and a stylish font to go along. The design must be creative, welcoming, and professional. I would like an island style theme for the website. This is a dating website so make sure that the design is tailored to that aspect.
Nice to have
- It would be nice to have a decorative font and a professional style on all the pages. Make sure the design will be mobile responsive and friendly for all the pages on the website.
Should not have
- The design should not be bland and uncreative.

```html
<!DOCTYPE html>
<html lang="en">
<head>
<meta charset="utf-8">
<title>Morvelique – Online Dating</title>
<link href="https://fonts.googleapis.com/css2?family=Lato:wght@400;700;900&family=Montserrat:wght@600;800&family=Open+Sans:wght@400;600;700&display=swap" rel="stylesheet">
<style>
:root{
  --orange:#f7941d;
  --teal:#2fb59f;
  --teal-dark:#23a08b;
  --ink:#2b2b2b;
  --text:#666;
  --muted:#999;
  --line:#e4e4e4;
  --white:#fff;
  --grey-head:#efedee;
}
*{margin:0;padding:0;box-sizing:border-box}
html,body{width:1200px;height:2894px;overflow:hidden}
body{position:relative;background:var(--white);font-family:"Open Sans",sans-serif;color:var(--text)}
.abs{position:absolute}
.center{text-align:center}

/* header */
.brand{left:135px;top:30px;display:flex;align-items:center;gap:10px;font-family:"Lato",sans-serif;font-weight:900;font-size:34px;color:var(--teal);white-space:nowrap}
.brand-dot{width:44px;height:44px;border-radius:50%;background:var(--orange)}
.nav{left:425px;top:46px;width:486px;display:flex;justify-content:space-between;font-family:"Open Sans",sans-serif;font-size:11px;font-weight:600;color:#333;white-space:nowrap}
.nav .active{color:var(--orange)}
.btn-login,.btn-register{top:36px;height:34px;line-height:34px;color:#fff;font-size:11px;font-weight:700;text-align:center}
.btn-login{left:930px;width:68px;background:var(--teal)}
.btn-register{left:1001px;width:67px;background:var(--orange)}

/* hero */
.hero{left:0;top:0;width:1200px;height:640px;background:linear-gradient(100deg,#f1efea 0%,#e3d4bd 30%,#a58a6a 55%,#6c5540 75%,#a98e72 100%)}
.hero-wave{left:0;top:570px}
.hero-title{left:560px;top:290px;width:540px;font-family:"Montserrat",sans-serif;font-weight:800;font-size:52px;line-height:64px;color:#fff;letter-spacing:1px;white-space:nowrap}
.hero-sub{left:560px;top:360px;width:540px;font-family:"Montserrat",sans-serif;font-weight:600;font-size:15px;color:#fff;line-height:31px;white-space:nowrap}
.dots{left:783px;top:442px;display:flex;gap:12px}
.dots span{width:15px;height:15px;border-radius:50%;border:2px solid #fff}
.dots .on{background:var(--orange)}

/* quick search */
.search{left:139px;top:150px;width:320px;height:425px;background:#fff;border:4px solid #d8cdb9;border-radius:22px;padding:28px 26px}
.search h3{text-align:center;font-family:"Lato",sans-serif;font-weight:900;font-size:22px;color:var(--orange);margin-bottom:24px}
.row{display:flex;gap:10px;margin-bottom:14px}
.field{flex:1}
.field label{display:block;font-size:12px;font-weight:600;color:#333;margin-bottom:6px}
.select{height:34px;border:1px solid #ddd;font-size:12px;color:#888;line-height:32px;padding-left:10px;position:relative}
.select::after{content:"";position:absolute;right:10px;top:12px;width:6px;height:6px;border-right:1px solid #999;border-bottom:1px solid #999;transform:rotate(45deg)}
.btn-search{display:block;margin:22px auto 0;width:108px;height:38px;line-height:38px;background:var(--orange);color:#fff;font-weight:700;font-size:12px;text-align:center}

/* safe dating */
.section-title{font-family:"Lato",sans-serif;font-weight:700;font-size:35px;color:var(--ink);width:1200px;left:0}
.feature{width:300px;text-align:center}
.feature .ring{width:104px;height:104px;margin:0 auto;border-radius:50%;border:2px solid var(--teal);padding:6px}
.feature .ring div{width:88px;height:88px;border-radius:50%;background:var(--orange);display:flex;align-items:center;justify-content:center}
.feature h4{font-family:"Lato",sans-serif;font-size:16px;color:var(--ink);margin:18px 0 8px}
.feature p{font-size:12px;line-height:21px;color:var(--text);padding:0 22px}
.divider{top:812px;height:230px;border-left:1px dashed #ccc}

/* promo band */
.promo{left:0;top:1077px;width:1200px;height:433px;background:radial-gradient(ellipse at 50% 50%,#5a4436 0%,#2c211c 55%,#160f0c 100%)}
.promo-title{left:0;top:1196px;width:1200px;font-family:"Lato",sans-serif;font-weight:700;font-size:35px;color:#fff}
.promo-sub{left:0;top:1253px;width:1200px;font-family:"Lato",sans-serif;font-size:18px;color:#fff;line-height:33px}
.btn-promo{left:440px;top:1347px;width:322px;height:36px;line-height:36px;background:var(--orange);color:#fff;font-weight:700;font-size:13px}

/* pricing */
.pricing-sub{left:0;top:1626px;width:1200px;font-size:10px;color:#555;letter-spacing:.3px}
.plan{background:#fff;box-shadow:0 1px 6px rgba(0,0,0,.15);text-align:center}
.plan .name{height:54px;line-height:54px;background:var(--grey-head);font-family:"Lato",sans-serif;font-weight:700;font-size:20px;color:#333}
.plan .price{background:var(--teal);color:#fff;height:112px;padding-top:20px}
.amount{font-family:"Lato",sans-serif;font-weight:700;font-size:40px}
.amount sup{font-size:18px;vertical-align:top;position:relative;top:6px;margin-right:6px}
.per{font-size:11px;margin-top:4px}
.plan ul{list-style:none;padding-top:34px;font-size:12.5px;color:#444;line-height:28px}
.plan .cta{display:inline-block;margin-top:32px;width:130px;height:34px;line-height:34px;background:var(--teal);color:#fff;font-weight:700;font-size:13px}
.plan-gold{z-index:2}
.plan-gold .price{background:var(--orange);height:195px;padding-top:24px;position:relative}
.plan-gold .price::after{content:"";position:absolute;left:50%;bottom:-14px;margin-left:-15px;border-left:15px solid transparent;border-right:15px solid transparent;border-top:14px solid var(--orange)}
.plan-gold .gname{font-family:"Lato",sans-serif;font-weight:700;font-size:17px;margin-bottom:12px}
.plan-gold .cta{background:var(--orange);margin-top:30px}

/* members */
.members{left:0;top:2213px;width:1200px;height:359px;background:var(--teal)}
.members-title{left:0;top:2268px;width:1200px;font-family:"Lato",sans-serif;font-weight:700;font-size:35px;color:#fff}
.member{width:180px;text-align:center;color:#fff}
.avatar{width:108px;height:108px;margin:0 auto;border-radius:50%;border:4px solid #1d8f7c;padding:3px;background:#fff}
.avatar div{width:100%;height:100%;border-radius:50%;background:linear-gradient(160deg,#d9b79a,#8c6a52)}
.member h5{font-family:"Lato",sans-serif;font-weight:700;font-size:13px;margin-top:20px}
.member p{font-size:11.5px;margin-top:6px}

/* footer */
.foot-brand{left:131px;top:2618px}
.foot-about{left:131px;top:2685px;width:250px;font-size:11.5px;line-height:21px;color:#555}
.foot-about a{display:block;margin-top:12px;color:var(--orange);text-decoration:none;font-size:11px}
.foot-head{top:2612px;font-family:"Lato",sans-serif;font-weight:700;font-size:17px;color:#333}
.links{left:434px;top:2650px;list-style:none;font-size:11.5px;line-height:24.5px;color:#555}
.email-input{left:594px;top:2652px;width:232px;height:40px;border:1px solid #ccc;font-size:11px;color:#aaa;line-height:38px;padding-left:10px}
.btn-sub{left:594px;top:2710px;width:102px;height:38px;line-height:38px;background:var(--orange);color:#fff;font-weight:700;font-size:12px;text-align:center}
.contact{left:893px;top:2652px;list-style:none;font-size:11.5px;color:#555}
.contact li{display:flex;gap:12px;margin-bottom:9px;line-height:20px}
.contact svg{flex:none;margin-top:3px}
.contact .mail{text-decoration:underline}
.foot-rule{left:131px;top:2832px;width:938px;border-top:1px solid var(--line)}
.copy{left:0;top:2852px;width:1200px;font-size:11.5px;color:#555}
</style>
</head>
<body>

<!-- hero -->
<div class="abs hero" role="img" aria-label="Photo of a couple embracing on a sunlit beach"></div>
<svg class="abs hero-wave" width="1200" height="110" viewBox="0 0 1200 110">
  <path d="M0 30 Q300 70 600 86 Q900 70 1200 30 L1200 110 L0 110 Z" fill="#fff"/>
  <path d="M0 30 Q300 70 600 86 Q900 70 1200 30" fill="none" stroke="#2fb59f" stroke-width="6"/>
</svg>

<div class="abs brand"><span class="brand-dot"></span>Morvelique</div>
<nav class="abs nav">
  <span class="active">HOME</span><span>SEARCH</span><span>MEMBERS</span><span>EXTRAS</span><span>ABOUT</span><span>PREMIUM</span><span>CONTACT</span>
</nav>
<div class="abs btn-login">LOGIN</div>
<div class="abs btn-register">REGISTER</div>

<div class="abs search">
  <h3>QUICK SEARCH</h3>
  <div class="row">
    <div class="field"><label>I am:</label><div class="select">Man</div></div>
    <div class="field"><label>Seeking a:</label><div class="select">Woman</div></div>
  </div>
  <div class="row">
    <div class="field"><label>Age:</label><div class="select">18</div></div>
    <div class="field"><label>To:</label><div class="select">99</div></div>
  </div>
  <div class="row">
    <div class="field"><label>Country</label><div class="select">Afghanistan</div></div>
  </div>
  <div class="btn-search">SEARCH &#9906;</div>
</div>

<div class="abs hero-title center">ONLINE DATING</div>
<div class="abs hero-sub center">LET'S FIND YOUR PERFECT MATCH TODAY<br>FIND YOUR PERFECT MATCH FOR FREE!</div>
<div class="abs dots"><span class="on"></span><span></span><span></span><span></span></div>

<!-- safe dating -->
<h2 class="abs section-title center" style="top:712px">100% Completely&nbsp; Safe Dating</h2>

<div class="abs feature" style="left:120px;top:808px">
  <div class="ring"><div>
    <svg width="44" height="44" viewBox="0 0 44 44"><circle cx="22" cy="22" r="20" fill="none" stroke="#fff" stroke-width="3"/><circle cx="22" cy="17" r="7" fill="#fff"/><path d="M10 35 Q22 20 34 35" fill="#fff"/></svg>
  </div></div>
  <h4>Create a Profile</h4>
  <p>Let people know all about you; the good and the quirky-show the world your true colors and find some one with the same unique qualities as you</p>
</div>
<div class="abs divider" style="left:434px"></div>
<div class="abs feature" style="left:452px;top:808px">
  <div class="ring"><div>
    <svg width="48" height="44" viewBox="0 0 48 44"><circle cx="18" cy="26" r="12" fill="none" stroke="#fff" stroke-width="3.5"/><circle cx="30" cy="26" r="12" fill="none" stroke="#fff" stroke-width="3.5"/><path d="M14 8 L18 3 L22 8 L18 12 Z" fill="#fff"/></svg>
  </div></div>
  <h4>Find Matches</h4>
  <p>Browse other users and feel the excitement of getting your first message and getting to know potential dates in a safe and fun environment.</p>
</div>
<div class="abs divider" style="left:774px"></div>
<div class="abs feature" style="left:784px;top:808px">
  <div class="ring"><div>
    <svg width="44" height="44" viewBox="0 0 44 44"><rect x="5" y="8" width="30" height="28" rx="2" fill="#fff"/><rect x="5" y="8" width="30" height="7" fill="#fde3c2"/><rect x="11" y="4" width="3" height="8" fill="#fff"/><rect x="26" y="4" width="3" height="8" fill="#fff"/><circle cx="33" cy="33" r="8" fill="#2fb59f"/><path d="M29 33 L32 36 L37 30" fill="none" stroke="#fff" stroke-width="2"/></svg>
  </div></div>
  <h4>Start Dating</h4>
  <p>Once you've found your potential soulmate, it's time to meet up and say 'Hello' to the start of your journey together</p>
</div>

<!-- promo -->
<div class="abs promo" role="img" aria-label="Photo of a smiling couple close together at night with soft city lights"></div>
<h2 class="abs promo-title center">Dating is EASY with Morvelique</h2>
<div class="abs promo-sub center">SIGN-UP FOR A 30 DAYS FREE TRIAL<br>ENJOY ALL THE BENEFITS MORVELIQUE HAS TO OFFER WITH A FULL MEMBERSHIP.</div>
<div class="abs btn-promo center">START MORVELIQUING WITH FREE SIGN-UP</div>

<!-- pricing -->
<h2 class="abs section-title center" style="top:1576px">Benefits</h2>
<div class="abs pricing-sub center">AFFORDABLE EASY SIGN-UP AND CANCELLATION PROCESSES</div>

<div class="abs plan" style="left:131px;top:1698px;width:297px;height:406px">
  <div class="name">SILVER</div>
  <div class="price"><div class="amount"><sup>$</sup>15/3</div><div class="per">$15/mo for 3 months</div></div>
  <ul><li>Eiusmod tempor incididunt</li><li>Aliquip commodo</li><li>Voluptatem accusantium</li><li>Adipisci velit, sed quia</li><li>Reprehenderit</li></ul>
  <span class="cta">SIGN UP NOW</span>
</div>
<div class="abs plan plan-gold" style="left:428px;top:1673px;width:344px;height:456px">
  <div class="price"><div class="gname">GOLD</div><div class="amount"><sup>$</sup>10/6</div><div class="per" style="margin-top:16px">$10/mo for 6 months</div></div>
  <ul><li>Eiusmod tempor incididunt</li><li>Aliquip commodo</li><li>Voluptatem accusantium</li><li>Adipisci velit, sed quia</li><li>Reprehenderit</li></ul>
  <span class="cta">SIGN UP NOW</span>
</div>
<div class="abs plan" style="left:772px;top:1698px;width:297px;height:406px">
  <div class="name">PLATINUM</div>
  <div class="price"><div class="amount"><sup>$</sup>5/12</div><div class="per">$5/mo for 12 months</div></div>
  <ul><li>Eiusmod tempor incididunt</li><li>Aliquip commodo</li><li>Voluptatem accusantium</li><li>Adipisci velit, sed quia</li><li>Reprehenderit</li></ul>
  <span class="cta">SIGN UP NOW</span>
</div>

<!-- latest members -->
<div class="abs members"></div>
<h2 class="abs members-title center">Last 5 Registered Users</h2>
<div class="abs member" style="left:114px;top:2344px"><div class="avatar"><div role="img" aria-label="Member profile photo"></div></div><h5>ALEX MORENO</h5><p>Lorem ipsum dolor sit amet</p></div>
<div class="abs member" style="left:313px;top:2344px"><div class="avatar"><div role="img" aria-label="Member profile photo"></div></div><h5>ALEX MORENO</h5><p>Lorem ipsum dolor sit amet</p></div>
<div class="abs member" style="left:512px;top:2344px"><div class="avatar"><div role="img" aria-label="Member profile photo"></div></div><h5>ALEX MORENO</h5><p>Lorem ipsum dolor sit amet</p></div>
<div class="abs member" style="left:711px;top:2344px"><div class="avatar"><div role="img" aria-label="Member profile photo"></div></div><h5>ALEX MORENO</h5><p>Lorem ipsum dolor sit amet</p></div>
<div class="abs member" style="left:910px;top:2344px"><div class="avatar"><div role="img" aria-label="Member profile photo"></div></div><h5>ALEX MORENO</h5><p>Lorem ipsum dolor sit amet</p></div>

<!-- footer -->
<div class="abs brand foot-brand"><span class="brand-dot"></span>Morvelique</div>
<div class="abs foot-about">Morvelique aims to provide a straight-forward, easy-to-use online dating service. I won't over-complicate things or reduce the amount of people you can talk to with<a>Read More »</a></div>

<div class="abs foot-head" style="left:434px">Quick Links</div>
<ul class="abs links"><li>About</li><li>Contact</li><li>Login</li><li>Members</li><li>Premium</li><li>Register</li></ul>

<div class="abs foot-head" style="left:594px">Subscribe for Updates</div>
<div class="abs email-input">Enter Email Address</div>
<div class="abs btn-sub">SUBSCRIBE</div>

<div class="abs foot-head" style="left:893px">Contact Info</div>
<ul class="abs contact">
  <li><svg width="12" height="12" viewBox="0 0 12 12"><rect width="12" height="12" rx="2" fill="#f7941d"/><path d="M3 3 Q3 9 9 9 L9 7 L7 6.5 L6.5 7.5 Q4.5 6.5 4.5 5 L5.5 4.5 L5 3 Z" fill="#fff"/></svg>(555) 014-2290</li>
  <li><svg width="12" height="12" viewBox="0 0 12 12"><rect width="12" height="12" rx="2" fill="#f7941d"/><rect x="3" y="5" width="6" height="4" fill="#fff"/></svg>(555) 014-2290</li>
  <li><svg width="12" height="12" viewBox="0 0 12 12"><rect y="2" width="12" height="8" fill="#f7941d"/><path d="M0 2 L6 7 L12 2" fill="none" stroke="#fff"/></svg><span class="mail">hello@morvelique.com</span></li>
  <li><svg width="12" height="14" viewBox="0 0 12 14"><path d="M6 0 A5 5 0 0 1 11 5 Q11 8 6 14 Q1 8 1 5 A5 5 0 0 1 6 0Z" fill="#f7941d"/><circle cx="6" cy="5" r="2" fill="#fff"/></svg><span>#2868 Lorem ipsum dolor sit<br>amet, consectetur</span></li>
</ul>

<div class="abs foot-rule"></div>
<div class="abs copy center">Copyrights © 2017 , morvelique | All rights reserved.</div>

</body>
</html>
```